Pebble Hop - mobile play centre poster designs

Who are we - we are a mobile playground business that specialises in providing entertainment to children in a safe, clean environment either at home or in a function centre. Brief - create 4 different signs to be displayed on our playgrounds. Please find attached 3 photos from our competitors to use as a guide. Corflute sign - size A1 Toddler zone - size A1 Playground rules - size A4 No climbing - size 20cmx8cm sending through photos and documents now.
Colors
Designer to choose colors to be used in the design.
Requirements
Must have
- Colour, be very specific with the rules, pictures

```html
<!DOCTYPE html>
<html lang="en">
<head>
<meta charset="utf-8">
<title>Pebble Hop – Toddler Zone Sign</title>
<link rel="stylesheet" href="https://fonts.googleapis.com/css2?family=Archivo+Black&family=Noto+Sans:ital,wght@0,800;1,700;1,800&display=swap">
<style>
  :root {
    --green: #00a651;
    --red: #ed1c24;
    --ink: #0a0a0a;
    --white: #ffffff;
    --skin: #f7c79c;
    --hair: #f6b73c;
    --suit: #fbd321;
    --sock: #1a1a1a;
    --sock-trim: #c8642e;
  }
  * { margin: 0; padding: 0; box-sizing: border-box; }
  html, body { width: 1200px; height: 419px; overflow: hidden; background: var(--white); }
  .sign-set { position: relative; width: 1200px; height: 419px; }

  .panel { position: absolute; top: 0; height: 419px; background: var(--green); }
  .panel__inner {
    position: absolute; left: 14px; right: 14px; top: 14px; bottom: 14px;
    background: var(--white); overflow: hidden;
  }
  .panel--zone { left: 0; width: 593px; }
  .panel--notice { left: 607px; width: 593px; }

  .headline {
    position: absolute; left: 0; width: 100%; text-align: center;
    font-family: "Archivo Black", "Arial Black", sans-serif;
    color: var(--green); font-size: 59px; line-height: 1;
  }
  .headline--top { top: 19px; }
  .headline--bottom { top: 89px; }

  .age-line {
    position: absolute; left: 22px; top: 160px; white-space: nowrap;
    font-family: "Archivo Black", "Arial Black", sans-serif;
    font-size: 49px; line-height: 1; color: var(--ink); letter-spacing: -0.4px;
  }
  .age-line .only { color: var(--red); }

  .art { position: absolute; border-radius: 40%; }
  .art--girl { left: 8px; top: 9px; width: 94px; height: 135px;
    background: linear-gradient(180deg, var(--hair) 0%, var(--skin) 55%, #f1e8cf 100%); }
  .art--boy { left: 436px; top: 16px; width: 116px; height: 135px;
    background: linear-gradient(180deg, #c9772b 0%, var(--skin) 40%, var(--suit) 100%); }

  .rule-box { position: absolute; top: 213px; height: 170px; border: 7px solid var(--red); }
  .rule-box--supervision { left: 8px; width: 322px; }
  .rule-box--socks { left: 340px; width: 213px; }
  .rule-box__text {
    position: absolute;
    font-family: "Noto Sans", Verdana, sans-serif; font-weight: 800;
    color: var(--ink); white-space: nowrap;
  }
  .rule-box--supervision .rule-box__text {
    left: 15px; top: 11px; font-size: 23.5px; line-height: 26.7px; letter-spacing: 0.3px;
  }
  .rule-box--socks .rule-box__text {
    left: 7px; top: 8px; font-size: 23px; line-height: 26.5px; letter-spacing: 0.3px;
  }
  .art--carer { left: 171px; top: 21px; width: 133px; height: 134px; border-radius: 30%;
    background: linear-gradient(160deg, #e9c98a 0%, #e8664c 45%, #f6d65a 100%); }
  .art--socks { left: 65px; top: 69px; width: 96px; height: 81px; border-radius: 25%;
    background: linear-gradient(180deg, var(--sock-trim) 0%, var(--sock) 40%, var(--sock) 80%, var(--sock-trim) 100%); }

  .notice {
    position: absolute; left: 0; width: 100%; text-align: center;
    font-family: "Noto Sans", Verdana, sans-serif; font-style: italic; font-weight: 800;
    font-size: 26.5px; color: var(--ink); white-space: nowrap;
  }
  .notice--use { top: 31px; line-height: 32.6px; }
  .notice--reason { top: 141px; line-height: 33px; }
  .notice .alert { color: var(--red); }
</style>
</head>
<body>
<main class="sign-set">
  <section class="panel panel--zone">
    <div class="panel__inner">
      <div class="art art--girl" role="img" aria-label="Illustration of a smiling blonde toddler girl"></div>
      <div class="art art--boy" role="img" aria-label="Illustration of a sitting toddler boy in a yellow outfit"></div>
      <h1 class="headline headline--top">TODDLER</h1>
      <div class="headline headline--bottom">ZONE</div>
      <p class="age-line">0-3 year olds <span class="only">ONLY</span></p>

      <div class="rule-box rule-box--supervision">
        <p class="rule-box__text">Supervision<br>required<br>at all times</p>
        <div class="art art--carer" role="img" aria-label="Illustration of a parent holding a toddler"></div>
      </div>
      <div class="rule-box rule-box--socks">
        <p class="rule-box__text">Parents please<br>wear socks too</p>
        <div class="art art--socks" role="img" aria-label="Illustration of a pair of patterned socks"></div>
      </div>
    </div>
  </section>

  <section class="panel panel--notice">
    <div class="panel__inner">
      <p class="notice notice--use">If using the toddler soft play equipment,<br>please ensure that this area is<br><span class="alert">used by children 0-3 ONLY</span>.</p>
      <p class="notice notice--reason">The <span class="alert">equipment and ball pit</span> is only<br>designed <span class="alert">for small children</span> and bigger<br>kids might injure themselves, the<br>smaller children or cause extensive<br>damage to the equipment, of which there<br>will be a charge back to the client.</p>
    </div>
  </section>
</main>
</body>
</html>
```